Software design for senior-friendly computer

Our software helps elderly people use the computer even if they are afraid of technology and have never used a computer before. We install the software on a Windows PC and our software holds a number of applications for basic tasks.

The software is old and needs a facelift to become more light and modern, and to avoid patronizing the audience. But the new design must still be "friendly", non-technical and make the user feel safe if he/she is a bit afraid of computers.

The screen resolution is 1600x900. This is not a complete redo of the software, so please avoid moving the buttons and other objects around.

We need your redesign of attached 6 screenshots (2 of which are the main menu). The rest of the apps we plan to do ourselves based on the winning design.

Target Market(s)

Age group 50+

Industry/Entity Type

Computer

Font styles to use
Sans Serif

Requirements
Must have
• Friendly, modern (but not too modern) look. Must make the user feel safe and comfortable using the computer even if he/she is a bit afraid of technology.
• Design must include the red/yellow mibo- logo shown in the screenshots.

```html
<!DOCTYPE html>
<html lang="en">
<head>
<meta charset="utf-8">
<title>mibo – Mail</title>
<link href="https://fonts.googleapis.com/css2?family=Open+Sans:wght@400;600&family=Arimo&display=swap" rel="stylesheet">
<style>
:root{
  --red:#cf1f1f;
  --white:#ffffff;
  --panel:#eeeeee;
  --btn-top:#f3f3f3;
  --btn-bottom:#d9d9d9;
  --ink:#222222;
  --orange:#e2531c;
  --orange-text:#f7a864;
  --orange-edge:#f07a3c;
  --yellow:#f7bf14;
  --list:#0c0c0c;
  --item-dark:#262626;
}
*{box-sizing:border-box;margin:0;padding:0}
html,body{width:1200px;height:675px;overflow:hidden}
body{font-family:"Open Sans",sans-serif;color:var(--ink);
  background:linear-gradient(90deg,#0e0e0e 0%,#2a2a2a 55%,#5a5a5a 100%);position:relative}
.abs{position:absolute}

/* header */
.topbar{left:0;top:0;width:1200px;height:75px;background:var(--red);box-shadow:0 2px 6px rgba(0,0,0,.5)}
.home{left:0;top:0;width:101px;height:75px;color:var(--white);text-align:center;font-size:20px;line-height:1}
.home svg{display:block;margin:10px auto 4px}
.brand{left:101px;top:0;width:185px;height:75px;background:var(--white);display:flex;align-items:center;justify-content:center}
.brand-name{font-size:30px;font-weight:400;color:var(--ink)}
.clock{left:436px;top:6px;width:300px;text-align:center;color:var(--white);line-height:1.1}
.clock .time{font-size:29px}
.clock .date{font-size:22px}
.user{right:104px;top:10px;text-align:right;color:var(--white);line-height:1.15}
.user .name{font-size:24px}
.user .mail{font-size:19px}
.avatar{left:1117px;top:2px;width:70px;height:70px;border-radius:50%;background:linear-gradient(180deg,#8a93a8,#4c5670);border:2px solid #dfe3ea}

/* mailbox column */
.box-head{background:var(--panel);display:flex;align-items:center;gap:16px;padding-left:13px;font-size:20px}
.received{left:15px;top:99px;width:291px;height:39px}
.list{left:15px;top:138px;width:291px;height:420px;background:var(--list)}
.mail-item{width:291px;height:48px;padding:2px 0 0 62px;position:absolute;left:0;overflow:hidden;white-space:nowrap}
.mail-item svg{position:absolute;left:13px;top:12px}
.mail-item .sender{font-size:14px;line-height:1.2}
.mail-item .subject{font-size:18px;line-height:1.2}
.mail-item.selected{top:1px;background:var(--white);border:3px solid var(--yellow)}
.mail-item.unread{top:50px;height:49px;background:var(--item-dark);color:var(--white);border:1px solid #555}
.sent{left:15px;top:620px;width:291px;height:38px}

.pager{background:var(--red)}
.pager-left{left:15px;top:558px;width:291px;height:46px}
.btn-orange{position:absolute;background:var(--orange);border:2px solid var(--orange-edge);color:var(--orange-text);
  display:flex;align-items:center;justify-content:center;gap:6px;font-size:19px}
.btn-orange .arrow{width:20px;height:20px;border-radius:50%;background:var(--orange-text);display:flex;align-items:center;justify-content:center}

/* reader */
.reader-head{left:322px;top:99px;width:556px;height:112px;background:var(--panel)}
.label{position:absolute;left:15px;font-size:17px}
.field{position:absolute;left:88px;background:var(--white);height:21px;padding-left:6px;font-size:15px;line-height:21px;white-space:nowrap}
.field small{font-size:12px}
.sent-date{position:absolute;right:20px;top:7px;text-align:right;font-size:16px;line-height:1.25}
.reader-body{left:322px;top:211px;width:556px;height:395px;background:var(--white);padding:14px 10px 0 10px;
  font-family:"Arimo",Arial,sans-serif;font-size:13px;line-height:15.8px;text-align:justify;color:#111}
.reader-body p{margin-bottom:14px}
.pager-center{left:322px;top:606px;width:556px;height:53px}

/* actions */
.help{left:894px;top:99px;width:290px;height:83px;background:var(--white);display:flex;align-items:center;gap:18px;padding-left:16px;font-size:16px;line-height:1.25}
.help .info{flex:none;width:45px;height:45px;border-radius:50%;background:var(--yellow);color:var(--white);font-size:28px;font-weight:600;display:flex;align-items:center;justify-content:center}
.action{left:893px;width:291px;height:43px;background:linear-gradient(180deg,var(--btn-top),var(--btn-bottom));display:flex;align-items:center;font-size:22px;gap:14px;padding-left:16px}
.action svg{flex:none}
</style>
</head>
<body>

<header>
  <div class="abs topbar"></div>
  <div class="abs home">
    <svg width="40" height="32" viewBox="0 0 40 32"><path d="M20 2 2 17h5v13h10v-9h6v9h10V17h5z" fill="#fff"/><rect x="28" y="4" width="4" height="8" fill="#fff"/></svg>
    Home
  </div>
  <div class="abs brand"><span class="brand-name">mibo</span></div>
  <div class="abs clock"><div class="time">09:39:50 AM</div><div class="date">Tuesday 02/14/2017</div></div>
  <div class="abs user"><div class="name">Henrik Vestergaard</div><div class="mail">hve@mibomail.dk</div></div>
  <div class="abs avatar" role="img" aria-label="User profile picture placeholder"></div>
</header>

<section class="mailbox">
  <div class="abs box-head received">
    <svg width="34" height="30" viewBox="0 0 34 30"><rect x="1" y="9" width="32" height="20" fill="#f7bf14"/><path d="M1 9l16 11 16-11" fill="none" stroke="#d99a00" stroke-width="2"/><path d="M17 0v12M11 7l6 6 6-6" stroke="#2fa84f" stroke-width="4" fill="none"/></svg>
    Received mail
  </div>
  <div class="abs list">
    <div class="mail-item selected">
      <svg width="34" height="24" viewBox="0 0 34 24"><rect width="34" height="24" fill="#f7bf14"/><path d="M0 0l17 13L34 0M0 24l12-12M34 24 22 12" fill="none" stroke="#fff" stroke-width="2"/></svg>
      <div class="sender">Henrik Vestergaard &lt;vestergaard.henrik@postmail.net&gt;</div>
      <div class="subject">Happy Birthday</div>
    </div>
    <div class="mail-item unread">
      <svg width="34" height="24" viewBox="0 0 34 24"><rect width="34" height="24" fill="#f7bf14"/><path d="M0 0l17 13L34 0M0 24l12-12M34 24 22 12" fill="none" stroke="#b58400" stroke-width="2"/></svg>
      <div class="sender">mibopc &lt;customerservice@mibopc.dk&gt;</div>
      <div class="subject">Welcome to miboPC</div>
    </div>
  </div>
  <div class="abs pager pager-left">
    <div class="btn-orange" style="left:14px;top:5px;width:97px;height:33px">Up <span class="arrow"><svg width="12" height="12" viewBox="0 0 12 12"><path d="M6 1 1 7h3v4h4V7h3z" fill="#e2531c"/></svg></span></div>
    <div class="btn-orange" style="left:179px;top:5px;width:104px;height:33px">Down <span class="arrow"><svg width="12" height="12" viewBox="0 0 12 12"><path d="M6 11 1 5h3V1h4v4h3z" fill="#e2531c"/></svg></span></div>
  </div>
  <div class="abs box-head sent">
    <svg width="34" height="26" viewBox="0 0 34 26"><rect x="1" y="6" width="30" height="19" fill="#f7bf14"/><path d="M1 6l15 10 15-10" fill="none" stroke="#d99a00" stroke-width="2"/><path d="M10 7h16M20 1l7 6-7 6" stroke="#1f5fd6" stroke-width="4" fill="none"/></svg>
    Sent mail
  </div>
</section>

<main>
  <div class="abs reader-head">
    <span class="label" style="top:13px">From</span>
    <span class="label" style="top:43px">To</span>
    <span class="label" style="top:75px">Subject</span>
    <div class="field" style="top:10px;width:350px">Henrik Vestergaard <small>&lt;vestergaard.henrik@postmail.net&gt;</small></div>
    <div class="field" style="top:42px;width:350px">Henrik Vestergaard <small>&lt;hve@mibomail.dk&gt;</small></div>
    <div class="field" style="top:75px;width:428px">Happy Birthday</div>
    <div class="sent-date">14 Feb<br>2017<br>10:00 AM</div>
  </div>
  <article class="abs reader-body">
    <p>Lorem ipsum dolor sit amet, consectetur adipiscing elit. Nunc facilisis ornare tortor et posuere. Vivamus bibendum lacus non ex maximus feugiat. Donec eu erat lobortis, dapibus diam non, laoreet urna. Aenean pharetra massa nisi, vitae pulvinar ligula tristique ut. Fusce in quam quis elit aliquet hendrerit eget non nisl. Maecenas sagittis bibendum eleifend. Class aptent taciti sociosqu ad litora torquent per conubia nostra, per inceptos himenaeos. Maecenas lacus nisl, vulputate at eleifend vitae, efficitur quis mi. Aenean fermentum lectus in nunc luctus bibendum. Donec rhoncus arcu sit amet hendrerit dignissim.</p>
    <p>Maecenas lacinia pulvinar dui, imperdiet iaculis neque ultrices eu. Pellentesque placerat efficitur orci vel scelerisque. Integer porta lectus felis, ut varius velit ultricies sed. Suspendisse eget leo vel orci auctor varius et ac nisi. Cras laoreet quam eget nisi imperdiet, accumsan hendrerit enim porttitor. Proin porttitor arcu quis facilisis feugiat. Nam a est tempor, efficitur urna vel, porttitor augue. Nam sem ligula, venenatis porta fringilla quis, egestas sed nibh. Duis sit amet sodales leo. Quisque porttitor neque vitae placerat tristique.</p>
    <p>Maecenas at urna nec nisl rutrum cursus non nec dui. Proin sed lectus eget felis laoreet accumsan. Integer eget lacus at massa ullamcorper euismod. Duis faucibus, justo ac placerat posuere, ante nunc ullamcorper orci, vel luctus nunc neque ac elit. Maecenas a porta velit. Aliquam at felis ac nisl sodales dignissim in vel eros. Praesent volutpat varius est, nec condimentum ante dictum sed. Vestibulum non auctor turpis, quis congue est. Quisque faucibus aliquet nulla non mollis. Maecenas luctus, odio sed posuere aliquet, urna lacus pulvinar diam, sed faucibus lorem augue ac nibh. Suspendisse consequat mi id arcu venenatis, in tincidunt quam ornare.</p>
  </article>
  <div class="abs pager pager-center">
    <div class="btn-orange" style="left:10px;top:8px;width:114px;height:38px;font-size:21px">Up <span class="arrow"><svg width="12" height="12" viewBox="0 0 12 12"><path d="M6 1 1 7h3v4h4V7h3z" fill="#e2531c"/></svg></span></div>
    <div class="btn-orange" style="left:422px;top:8px;width:122px;height:38px;font-size:21px">Down <span class="arrow"><svg width="12" height="12" viewBox="0 0 12 12"><path d="M6 11 1 5h3V1h4v4h3z" fill="#e2531c"/></svg></span></div>
  </div>
</main>

<aside>
  <div class="abs help"><span class="info">i</span><span>Click the interactive<br>guide for help on e-mail</span></div>
  <div class="abs action" style="top:190px">
    <svg width="26" height="26" viewBox="0 0 26 26"><path d="M4 22l2-7L19 2l5 5L11 20z" fill="#d8232a"/><path d="M4 22l2-7 5 5z" fill="#f2c49a"/></svg>Compose</div>
  <div class="abs action" style="top:240px">
    <svg width="26" height="26" viewBox="0 0 26 26"><path d="M11 5 2 12l9 7v-4c6 0 10 2 13 6-1-7-5-11-13-11z" fill="#2fa84f"/></svg>Reply</div>
  <div class="abs action" style="top:290px">
    <svg width="26" height="26" viewBox="0 0 26 26"><rect x="2" y="4" width="22" height="20" fill="#3b9ad9"/><path d="M14 9l6 5-6 5v-3c-4 0-6 1-8 3 1-4 3-6 8-7z" fill="#fff"/></svg>Forward</div>
  <div class="abs action" style="top:341px">
    <svg width="26" height="26" viewBox="0 0 26 26"><path d="M4 6h18M10 6V3h6v3M6 8l1 16h12l1-16" fill="none" stroke="#555" stroke-width="2"/><path d="M10 11v10M13 11v10M16 11v10" stroke="#555" stroke-width="1.6"/></svg>Delete</div>
  <div class="abs action" style="top:390px">
    <svg width="26" height="26" viewBox="0 0 26 26"><rect x="7" y="2" width="12" height="7" fill="#c9c9c9"/><rect x="2" y="9" width="22" height="10" rx="2" fill="#c02a2a"/><rect x="7" y="15" width="12" height="9" fill="#eee" stroke="#888"/></svg>Print</div>
  <div class="abs action" style="top:440px">
    <svg width="26" height="26" viewBox="0 0 26 26"><rect x="2" y="2" width="22" height="23" rx="2" fill="#222"/><circle cx="13" cy="14" r="7" fill="none" stroke="#fff" stroke-width="2"/><circle cx="13" cy="14" r="2.5" fill="none" stroke="#fff" stroke-width="1.8"/></svg>Address Book</div>
</aside>

</body>
</html>
```